Halvery Construction Group Website

Need a dynamic corporate website that can be built on with time. We want to get our information out to the world and have a place where customers can submit requests for proposals.

Target Market(s)

Custom home owners and buyers. Architects and Real Estate Agents.

Industry/Entity Type

Construction

Number of Pages Required

3 page

Font styles to use
Serif
Sans Serif

Requirements
Must have
• Company logo, about, company contact information, biography, contact, projects,
• Sleek, modern, clean, attractive design.
• Online form customers can use for filling out a request for project proposal.
• Linkedin hyperlink.
• Uses www.halveryconstructiongroup.example

```html
<!DOCTYPE html>
<html lang="en">
<head>
<meta charset="utf-8">
<title>Halvery Construction Group</title>
<link rel="stylesheet" href="https://fonts.googleapis.com/css2?family=Exo+2:wght@500;600;700&family=Arimo:wght@400;700&display=swap">
<style>
  :root {
    --navy: #0b3f8c;
    --royal: #00509b;
    --ink: #555b63;
    --muted: #6b7077;
    --paper: #f5f7f9;
    --white: #ffffff;
    --nav-active: #0a4fa0;
  }
  * { box-sizing: border-box; margin: 0; padding: 0; }
  html, body { width: 1200px; height: 909px; overflow: hidden; }
  body { position: relative; background: var(--paper); font-family: "Arimo", Arial, sans-serif; }

  .hero { position: absolute; left: 0; top: 0; width: 1200px; height: 608px; overflow: hidden; }
  .hero-site {
    position: absolute; inset: 0;
    background:
      radial-gradient(ellipse 420px 260px at 330px 560px, rgba(60,110,120,0.35), transparent 70%),
      radial-gradient(ellipse 500px 300px at 120px 120px, rgba(40,110,200,0.55), transparent 70%),
      linear-gradient(175deg, #1a60b2 0%, #134f9f 40%, #0d3c85 75%, #0a3274 100%);
  }
  .hero-skyline {
    position: absolute; inset: 0;
    clip-path: polygon(542px 0, 1200px 0, 1200px 608px, 669px 608px);
    background:
      radial-gradient(ellipse 300px 180px at 1080px 60px, rgba(150,210,240,0.45), transparent 70%),
      radial-gradient(ellipse 380px 200px at 900px 560px, rgba(20,80,150,0.45), transparent 70%),
      linear-gradient(180deg, #4aa2dc 0%, #3590cf 35%, #2a7fc2 65%, #2068ae 100%);
  }

  .brand { position: absolute; left: 86px; top: 44px; display: flex; align-items: center; gap: 12px; }
  .brand-square { width: 60px; height: 57px; background: var(--white); border-radius: 8px; }
  .brand-name { font-family: "Exo 2", sans-serif; font-weight: 600; font-size: 42px; color: var(--white); letter-spacing: 1px; line-height: 1; }

  .nav { position: absolute; top: 64px; left: 603px; font-family: "Exo 2", sans-serif; font-weight: 600; font-size: 14px; }
  .nav a { position: absolute; color: var(--white); text-decoration: none; white-space: nowrap; }
  .nav a.active { color: var(--nav-active); }
  .search {
    position: absolute; left: 1067px; top: 49px; width: 48px; height: 48px;
    border: 2px solid var(--white); border-radius: 50%;
    display: flex; align-items: center; justify-content: center;
  }

  .emblem {
    position: absolute; left: 531px; top: 245px; width: 138px; height: 138px;
    background: var(--white); border-radius: 50%;
    display: flex; align-items: center; justify-content: center;
    font-family: "Exo 2", sans-serif; font-weight: 600; font-size: 18px; color: var(--royal); letter-spacing: 1px;
  }

  .links { position: absolute; left: 0; top: 608px; width: 1200px; height: 241px; background: var(--paper); }
  .links h3 {
    position: absolute; top: 33px; font-family: "Exo 2", sans-serif; font-weight: 500;
    font-size: 18.5px; color: var(--ink); letter-spacing: 1px; white-space: nowrap;
  }
  .links ul { position: absolute; top: 72px; list-style: none; }
  .links li { font-size: 12.4px; color: var(--muted); height: 28.3px; padding-left: 19px; position: relative; }
  .links li::before { content: "\00BB"; position: absolute; left: 0; top: -1px; font-size: 12px; color: var(--muted); }
  .col-projects { left: 86px; }
  .col-profile { left: 250px; }
  .col-connect { left: 404px; }
  .solutions { left: 577px; }
  .solutions-text {
    position: absolute; left: 581px; top: 80px; width: 525px;
    font-size: 12.4px; line-height: 24px; color: var(--muted);
  }

  .footer-bar { position: absolute; left: 0; top: 849px; width: 1200px; height: 60px; background: var(--royal); }
  .copyright { position: absolute; left: 87px; top: 22px; font-size: 12.4px; color: var(--white); }
  .social {
    position: absolute; top: 12px; width: 37px; height: 37px;
    border: 2px solid var(--white); border-radius: 50%;
    display: flex; align-items: center; justify-content: center;
    font-family: "Arimo", Arial, sans-serif; font-weight: 700; font-size: 9px; color: var(--white);
    text-decoration: none; letter-spacing: 0.3px;
  }
</style>
</head>
<body>
  <header class="hero">
    <div class="hero-site" role="img" aria-label="Photo of a worker on scaffolding at a construction site, tinted deep blue"></div>
    <div class="hero-skyline" role="img" aria-label="Photo of a city skyline with high-rise towers, tinted light blue"></div>

    <div class="brand">
      <span class="brand-square"></span>
      <span class="brand-name">HALVERY</span>
    </div>

    <nav class="nav">
      <a class="active" style="left:0">HOME</a>
      <a style="left:85px">ABOUT</a>
      <a style="left:177px">BIO</a>
      <a style="left:245px">PROJECTS</a>
      <a style="left:361px">CONTACT US</a>
    </nav>
    <a class="search" aria-label="Search">
      <svg width="14" height="14" viewBox="0 0 14 14" aria-hidden="true">
        <circle cx="5.8" cy="5.8" r="4.3" fill="none" stroke="#ffffff" stroke-width="2"/>
        <line x1="9" y1="9" x2="12.8" y2="12.8" stroke="#ffffff" stroke-width="2.2" stroke-linecap="round"/>
      </svg>
    </a>

    <div class="emblem">HALVERY</div>
  </header>

  <section class="links">
    <h3 class="col-projects">PROJECTS</h3>
    <ul class="col-projects">
      <li>Commercial</li><li>Residential</li><li>Community</li><li>Location Map</li>
    </ul>

    <h3 class="col-profile">PROFILE</h3>
    <ul class="col-profile">
      <li>Team</li><li>Process</li><li>Testimonials</li><li>History</li>
    </ul>

    <h3 class="col-connect">CONNECT</h3>
    <ul class="col-connect">
      <li>Home</li><li>About,</li><li>Bio</li><li>Projects</li><li>Contact us</li>
    </ul>

    <h3 class="solutions">COMMERCIAL, RESIDENTIAL AND COMMUNITY SOLUTIONS</h3>
    <p class="solutions-text">Sed ut perspiciatis unde omnis iste natus error sit voluptatem accusantium doloremque laudan tium, totam rem aperiam, eaque ipsa quae ab illo inventore veritatis et quasi architecto beatae vit ae dicta sunt explicabo. Nemo enim ipsam voluptatem quia voluptas sit aspernatur aut dolores eos qui ratione voluptatem sequi nesciunt.</p>
  </section>

  <footer class="footer-bar">
    <p class="copyright">© 2016 Copyrights.Halvery Construction Group.All Rights Reserved.</p>
    <a class="social" style="left:907px" aria-label="Social page">SOC</a>
    <a class="social" style="left:950px" aria-label="News feed">FEED</a>
    <a class="social" style="left:993px" aria-label="Photo gallery">PICS</a>
    <a class="social" style="left:1035px" aria-label="Professional network profile">PRO</a>
    <a class="social" style="left:1078px" aria-label="Video channel">VID</a>
  </footer>
</body>
</html>
```